Hop Bright Meadow Business Website Branding

Looking for a wordpress template design with CSS and HTML encoding. Current website can be seen at hopbrightmeadow.example.

WE ARE CURRENTLY IN PROCESS GETTING A LOGO DESIGN... I HAVE INCLUDED THE TOP POTENTIAL DESIGNS FOR REFERENCE TO HELP UNDERSTAND WHAT STYLE WE ARE LOOKING FOR...
NOTE: THE “PEBBLE CREW” LOGO WAS A PREVIOUS COMPANY WE OWNED SO YOU CAN GE A FEEL FOR THE TYPE OF DESIGNS WE HAVE USED IN THE PAST.

My blog will focus on making a connection with wild Florida, it’s wildlife, plants and animals... with an eye toward Florida conservation, nature adventure trips, and education... Content, photos and other merchandise will also be offered for sale.
I’m looking for a site design that incorporates Florida nature and wildlife/plants, with a fun “Old Florida” retro-adventure feel.
When they see this site it should speak to the import of natural Florida and the critical nature of the ecosystem here... while being instantly recognizable and iconic... IE: when I think of florida I think of water, plants, warmth, sunsets etc...

https://join.chatroomhub.example/t/lumexstudio-kzt4821/shared_invite/zt-pqwrt83m-hRnLvXaKoPzsYcB1Uq7JdM

Target Market(s)

Nature, Education, Conservation, Photography

Industry/Entity Type

Photographer

Coding

Coded - Design and coding required

Requirements
Must have
• Need to have site wide template design which generally includes a landing page and a general page template for other pages... Must include html and css encoding...
Should not have
• Any animals included in the site should be Florida native... IE: no African animals etc... This will require some research to ensure that if animals are included that they are part of the Florida ecosystem.

```html
<!DOCTYPE html>
<html lang="en">
<head>
<meta charset="utf-8">
<title>Hop Bright Meadow</title>
<link rel="stylesheet" href="https://fonts.googleapis.com/css2?family=Kaushan+Script&family=Poppins:wght@300;400;500&display=swap">
<style>
:root{
  --cream:#fdf9f1;
  --brown:#7b4a2d;
  --brown-dark:#5a3320;
  --band-1:#80533f;
  --band-2:#a57a62;
  --band-3:#c9ab93;
  --teal-1:#1b8f8c;
  --teal-2:#29a9a2;
  --teal-3:#0f5b5d;
  --ink:#2f2f2f;
  --muted:#555;
  --white:#fff;
  --sky:#1aa6e6;
  --products-bg:#ece5de;
  --black:#000;
}
*{margin:0;padding:0;box-sizing:border-box}
html,body{width:1200px;height:3911px;overflow:hidden}
body{position:relative;background:var(--cream);font-family:"Poppins",sans-serif;color:var(--ink)}
.abs{position:absolute}
.script{font-family:"Kaushan Script",cursive}

/* header */
.brand{left:172px;top:40px;display:flex;align-items:center;gap:14px;color:var(--white);font-size:26px;font-weight:500}
.brand-dot{width:46px;height:46px;border-radius:50%;background:var(--white);opacity:.9}
.nav{left:554px;top:48px;width:474px;display:flex;justify-content:space-between}
.nav a{font-family:"Kaushan Script",cursive;color:var(--white);font-size:27px;text-decoration:none}

/* hero */
.hero{left:0;top:0;width:1200px;height:770px}
.hero-title{left:175px;top:280px;font-size:76px;color:var(--white);text-shadow:0 3px 6px rgba(0,0,0,.35)}
.hero-text{left:174px;top:392px;width:500px;font-size:15.5px;line-height:31px;color:var(--white);text-align:justify}

/* about */
.eyebrow{font-family:"Kaushan Script",cursive;color:var(--brown);font-size:25px;text-transform:uppercase}
.heading{font-family:"Kaushan Script",cursive;color:var(--brown);font-size:58px;line-height:1}
.about-eyebrow{left:0;width:1200px;top:828px;text-align:center}
.about-title{left:0;width:1200px;top:872px;text-align:center}
.about-text{left:172px;top:962px;width:856px;font-size:15.5px;line-height:26px;text-align:center;color:var(--ink)}
.band{left:0;top:1230px;width:1200px;height:730px}
.falcon{left:930px;top:1400px;width:270px;height:470px;border-radius:50% 0 0 50%;background:radial-gradient(ellipse at 55% 45%,#d9d3c8 0%,#a08672 45%,rgba(165,122,98,0) 75%)}
.circle{border-radius:50%;border:5px solid var(--white);box-shadow:0 6px 14px rgba(0,0,0,.3);overflow:hidden;display:flex;align-items:flex-end;justify-content:center}
.circle span{font-family:"Kaushan Script",cursive;color:var(--white);font-size:34px;margin-bottom:26px;text-shadow:0 2px 4px rgba(0,0,0,.5)}
.c-wildlife{left:175px;top:1136px;width:258px;height:258px;background:linear-gradient(180deg,#f4c27a 0%,#e9a55a 55%,#6d4a30 100%)}
.c-adventure{left:453px;top:1121px;width:288px;height:288px;background:linear-gradient(180deg,#cfe0ea 0%,#e7d3b0 45%,#2d8e8a 100%)}
.c-education{left:769px;top:1136px;width:258px;height:258px;background:linear-gradient(180deg,#3f86d4 0%,#c48a62 45%,#2f7d6a 75%,#1f3c4e 100%)}
.portrait{left:172px;top:1481px;width:228px;height:345px;border-radius:30px;border:3px solid var(--white);background:linear-gradient(160deg,#f0b96d 0%,#c97a4a 40%,#2fb0c8 75%,#1c6f86 100%)}
.bio{left:427px;top:1492px;width:492px;font-size:13.8px;line-height:26.3px;color:var(--white);text-align:justify}
.bio p+p{margin-top:16px}

/* blog */
.blog-eyebrow{left:174px;top:1990px}
.blog-title{left:172px;top:2028px;font-size:60px}
.pager{left:942px;top:2026px;display:flex;gap:22px}
.post-img{left:173px;width:324px;height:251px;border-radius:28px;border:2px solid #ddd}
.post-img.p1{top:2137px;background:linear-gradient(180deg,#6e7a6a 0%,#d9b56a 40%,#3e4a33 70%,#25301e 100%)}
.post-img.p2{top:2418px;background:linear-gradient(180deg,#2e6bc0 0%,#8fb5d9 30%,#4f7a3a 60%,#2d4a22 100%)}
.post{left:529px;width:499px}
.post.p1{top:2163px}
.post.p2{top:2444px}
.post h3{font-weight:400;font-size:19px;color:var(--ink)}
.post .meta{font-size:13px;margin-top:8px;color:var(--ink);text-transform:uppercase}
.post .meta b{font-weight:400;color:var(--brown);text-transform:none}
.post p{font-size:13.6px;line-height:24.8px;margin-top:18px;text-align:justify;color:var(--muted)}

/* products */
.products{left:0;top:2746px;width:1200px;height:730px;background:linear-gradient(180deg,#ebe4dc 0%,#efe9e2 50%,#e4dcd2 100%)}
.prod-eyebrow{left:0;width:1200px;top:2800px;text-align:center}
.prod-title{left:0;width:1200px;top:2838px;text-align:center}
.card{top:2947px;width:252px;height:354px;background:var(--white);border:1px solid #ddd;display:flex;flex-direction:column;align-items:center}
.card .shot{width:130px;height:165px;margin-top:24px}
.card h4{font-weight:400;font-size:17px;margin-top:32px;color:var(--ink)}
.row{display:flex;align-items:center;gap:12px;margin-top:10px;width:200px}
.price{font-size:19px;color:var(--ink)}
.stars{color:var(--sky);font-size:19px;letter-spacing:3px}
.actions{display:flex;align-items:center;gap:8px;margin-top:14px}
.round{width:36px;height:36px;border-radius:50%;border:1.5px solid #333;display:flex;align-items:center;justify-content:center}
.cart-btn{background:var(--sky);color:var(--white);font-size:12px;border-radius:20px;padding:11px 12px}
.side-arrow{top:3117px}

/* footer */
.footer{left:0;top:3380px;width:1200px;height:531px}
.foot-brand{left:0;width:1200px;top:3575px;display:flex;justify-content:center;align-items:center;gap:14px;color:var(--white);font-size:32px;font-weight:500}
.social{left:0;width:1200px;top:3712px;display:flex;justify-content:center;gap:29px}
.social span{width:54px;height:54px;border-radius:50%;background:var(--white)}
.rule{left:172px;top:3817px;width:856px;height:1px;background:#cfcfcf}
.copy{left:0;width:1200px;top:3852px;text-align:center;color:var(--white);font-size:14.5px}
</style>
</head>
<body>

<svg class="abs hero" viewBox="0 0 1200 770" role="img" aria-label="Photo of a manatee swimming over a sandy spring floor in clear teal water">
  <defs>
    <linearGradient id="heroGrad" x1="0" y1="0" x2="0.3" y2="1">
      <stop offset="0" stop-color="#1c958f"/>
      <stop offset=".45" stop-color="#2aa39c"/>
      <stop offset=".8" stop-color="#3f8f85"/>
      <stop offset="1" stop-color="#0f5b5d"/>
    </linearGradient>
    <radialGradient id="glow" cx=".72" cy=".45" r=".35">
      <stop offset="0" stop-color="#7fa69a" stop-opacity=".55"/>
      <stop offset="1" stop-color="#7fa69a" stop-opacity="0"/>
    </radialGradient>
  </defs>
  <path d="M0 0H1200V728C1120 760 1020 770 940 745C840 712 780 690 700 700C600 712 560 745 460 745C370 745 330 700 220 700C120 700 60 740 0 770Z" fill="url(#heroGrad)"/>
  <path d="M0 0H1200V728C1120 760 1020 770 940 745C840 712 780 690 700 700C600 712 560 745 460 745C370 745 330 700 220 700C120 700 60 740 0 770Z" fill="url(#glow)"/>
</svg>

<div class="abs brand"><span class="brand-dot"></span>Hop Bright Meadow</div>
<nav class="abs nav">
  <a href="#">Home</a><a href="#">About</a><a href="#">Blog</a><a href="#">Places</a><a href="#">Contact</a>
</nav>

<h1 class="abs hero-title script">Hop Bright Meadow</h1>
<p class="abs hero-text">Come explore wild places and stunning scenery with me as I discover new and exciting eco-adventures and learn about the rare and unique wildlife</p>

<div class="abs about-eyebrow eyebrow">About</div>
<h2 class="abs about-title heading">Hop Bright Meadow</h2>
<p class="abs about-text">Come explore wild places and stunning scenery with me as I discover new and exciting eco-adventures and learn about the rare and unique wildlife and environments that make Florida so precious and extraordinary. I hope you can vicariously enjoy the wild and untamed beauty of Florida through my eyes, and learn some amazing things about nature on our explorations.</p>

<svg class="abs band" viewBox="0 0 1200 730" preserveAspectRatio="none">
  <defs>
    <linearGradient id="bandGrad" x1="0" y1="0" x2="1" y2="0">
      <stop offset="0" stop-color="var(--band-1)"/>
      <stop offset=".55" stop-color="var(--band-2)"/>
      <stop offset="1" stop-color="var(--band-3)"/>
    </linearGradient>
  </defs>
  <path d="M0 60C200 30 400 20 600 22C800 24 1000 15 1200 30V630C1000 660 820 715 600 715C380 715 180 650 0 623Z" fill="url(#bandGrad)"/>
</svg>
<div class="abs falcon" role="img" aria-label="Photo of a peregrine falcon perched on a branch"></div>

<div class="abs circle c-wildlife" role="img" aria-label="Photo of a heron silhouetted at sunset"><span>Wildlife</span></div>
<div class="abs circle c-adventure" role="img" aria-label="Photo of palm trees along a boardwalk"><span>Adventure</span></div>
<div class="abs circle c-education" role="img" aria-label="Photo of a university building and fountain"><span>Education</span></div>

<div class="abs portrait" role="img" aria-label="Portrait photo of the author on the beach"></div>
<div class="abs bio">
  <p>Hello nature lovers! I'm Marisol Thorne, a wildlife educator, Coastal Field Naturalist, nature writer and photographer, busy mama of three kiddos, a playful Havanese puppy, two very chubby guinea pigs, and a giant tree frog. I have a passion for all things nature and I adore living in Southwest Florida. I will always be a California girl, but from the moment I set foot in Florida, its wild beauty stole my heart.</p>
  <p>For the past 23 years, I have been fortunate to have some very unique and special experiences caring for many different species of animals and educating the public about wildlife and the environment. My hope is that those I endeavor to educate will better understand their connection with the natural world and our shared responsibility to protect Florida's wild and priceless beauty.</p>
</div>

<div class="abs blog-eyebrow eyebrow">My</div>
<h2 class="abs blog-title heading">Blog Post</h2>
<div class="abs pager" aria-label="Previous and next">
  <svg width="30" height="44" viewBox="0 0 30 44"><path d="M26 4L5 22L26 40" fill="none" stroke="var(--brown-dark)" stroke-width="4"/></svg>
  <svg width="30" height="44" viewBox="0 0 30 44"><path d="M4 4L25 22L4 40" fill="none" stroke="var(--brown-dark)" stroke-width="4"/></svg>
</div>

<div class="abs post-img p1" role="img" aria-label="Photo of a misty pine forest at sunrise"></div>
<article class="abs post p1">
  <h3>Coastal Field Naturalist Uplands Nature Journal</h3>
  <div class="meta">Posted on <b>october 12, 2020</b> &nbsp;By &nbsp;<b>marisol</b></div>
  <p>Since I was a child, my deepest spiritual connections with nature have come in the stillness as I hiked in the forest or listened to the waves crashing on the beach. Nature can calm and heal the soul, and re-charge one during troubled times. Family bonds can also be built and strength ened when out in nature.</p>
</article>

<div class="abs post-img p2" role="img" aria-label="Photo of tall pines and palmettos under a blue sky"></div>
<article class="abs post p2">
  <h3>Environmental Ethics Statement:</h3>
  <div class="meta">Posted on <b>october 12, 2020</b> &nbsp;By &nbsp;<b>marisol</b></div>
  <p>As a Coastal Field Naturalist, environmental interpreter, and nature writer, I will conduct my personal and professional life with integrity and strive to enlighten and educate the public about the natural world with enthusiasm, kindness, courtesy, dignity and respect. As a Coastal Field Naturalist, environmental interpreter, and nature writer.</p>
</article>

<div class="abs products" role="img" aria-label="Faint photo of an alligator in shallow water"></div>
<div class="abs prod-eyebrow eyebrow">Our</div>
<h2 class="abs prod-title heading">Products</h2>

<div class="abs card" style="left:172px">
  <div class="shot" role="img" aria-label="Framed print product photo" style="background:#f6f4ef;border:7px solid #b58b52"></div>
  <h4>PHOTOGRAPHY</h4>
  <div class="row"><span class="price">$20.00</span><span class="stars">★★★★☆</span></div>
  <div class="actions">
    <span class="round"><svg width="16" height="16" viewBox="0 0 16 16"><path d="M1 2h2l2 8h8l2-6H4" fill="none" stroke="#333" stroke-width="1.6"/><circle cx="6" cy="13.5" r="1.3" fill="#333"/><circle cx="12" cy="13.5" r="1.3" fill="#333"/></svg></span>
    <span class="round"><svg width="16" height="16" viewBox="0 0 16 16"><path d="M8 14S1.5 9.5 1.5 5.5A3 3 0 0 1 8 4a3 3 0 0 1 6.5 1.5C14.5 9.5 8 14 8 14Z" fill="none" stroke="#333" stroke-width="1.5"/></svg></span>
    <span class="cart-btn">ADD TO CART</span>
  </div>
</div>
<div class="abs card" style="left:474px">
  <div class="shot" role="img" aria-label="White baseball cap product photo" style="background:radial-gradient(ellipse at 50% 55%,#f2f2f2 0%,#d9d9d9 45%,#fff 70%)"></div>
  <h4>CAPS</h4>
  <div class="row"><span class="price">$20.00</span><span class="stars">★★★★☆</span></div>
  <div class="actions">
    <span class="round"><svg width="16" height="16" viewBox="0 0 16 16"><path d="M1 2h2l2 8h8l2-6H4" fill="none" stroke="#333" stroke-width="1.6"/><circle cx="6" cy="13.5" r="1.3" fill="#333"/><circle cx="12" cy="13.5" r="1.3" fill="#333"/></svg></span>
    <span class="round"><svg width="16" height="16" viewBox="0 0 16 16"><path d="M8 14S1.5 9.5 1.5 5.5A3 3 0 0 1 8 4a3 3 0 0 1 6.5 1.5C14.5 9.5 8 14 8 14Z" fill="none" stroke="#333" stroke-width="1.5"/></svg></span>
    <span class="cart-btn">ADD TO CART</span>
  </div>
</div>
<div class="abs card" style="left:775px">
  <div class="shot" role="img" aria-label="Black t-shirt product photo" style="background:radial-gradient(circle at 50% 40%,#e8b7a8 0%,#e8b7a8 14%,#111 15%,#111 60%,#fff 75%)"></div>
  <h4>TSHIRTS</h4>
  <div class="row"><span class="price">$20.00</span><span class="stars">★★★★☆</span></div>
  <div class="actions">
    <span class="round"><svg width="16" height="16" viewBox="0 0 16 16"><path d="M1 2h2l2 8h8l2-6H4" fill="none" stroke="#333" stroke-width="1.6"/><circle cx="6" cy="13.5" r="1.3" fill="#333"/><circle cx="12" cy="13.5" r="1.3" fill="#333"/></svg></span>
    <span class="round"><svg width="16" height="16" viewBox="0 0 16 16"><path d="M8 14S1.5 9.5 1.5 5.5A3 3 0 0 1 8 4a3 3 0 0 1 6.5 1.5C14.5 9.5 8 14 8 14Z" fill="none" stroke="#333" stroke-width="1.5"/></svg></span>
    <span class="cart-btn">ADD TO CART</span>
  </div>
</div>

<svg class="abs side-arrow" style="left:68px" width="32" height="48" viewBox="0 0 32 48"><path d="M28 4L5 24L28 44" fill="none" stroke="var(--brown-dark)" stroke-width="4"/></svg>
<svg class="abs side-arrow" style="left:1086px" width="32" height="48" viewBox="0 0 32 48"><path d="M4 4L27 24L4 44" fill="none" stroke="var(--brown-dark)" stroke-width="4"/></svg>

<svg class="abs footer" viewBox="0 0 1200 531" preserveAspectRatio="none">
  <path d="M0 60C90 20 160 40 260 45C380 50 470 10 600 15C740 20 800 60 930 55C1040 50 1120 20 1200 5V531H0Z" fill="var(--black)"/>
</svg>
<div class="abs foot-brand"><span class="brand-dot"></span>Hop Bright Meadow</div>
<div class="abs social" aria-label="Social links">
  <span></span><span></span><span></span><span></span><span></span>
</div>
<div class="abs rule"></div>
<p class="abs copy">Copyrights @ 2020 Hop Bright Meadow. all Rights Reserved.</p>

</body>
</html>
```